Private chef located in Vail, CO

I would like my info located at the top of the landing page, perhaps some Vail mountain landscapes that I could swap out from summer to winter photos. I need the menu bar to have a link to a blog, about me, photo gallery, recipes & beer reviews. I would also like to have a shop, but only populated with products from corvelle or other online retailers that I can affiliate with.
Extremely wealthy, affluent people, concierge, international
5+ page

```html
<!DOCTYPE html>
<html lang="en">
<head>
<meta charset="utf-8">
<title>Declan Hartwell — Private Chef in Vail</title>
<link href="https://fonts.googleapis.com/css2?family=Montserrat:wght@400;500&family=Open+Sans:wght@400;600;700&display=swap" rel="stylesheet">
<style>
  :root {
    --sky-deep: #12307f;
    --sky-mid: #21479b;
    --slope-blue: #4a6aa8;
    --snow-shade: #8ea3c9;
    --snow-light: #b7c5de;
    --accent: #f4782f;
    --star: #f7d21a;
    --white: #ffffff;
  }
  * { margin: 0; padding: 0; box-sizing: border-box; }
  html, body { width: 1200px; height: 730px; overflow: hidden; }
  body {
    position: relative;
    font-family: "Open Sans", Arial, sans-serif;
    color: var(--white);
  }
  .hero-backdrop {
    position: absolute; inset: 0;
    background:
      linear-gradient(180deg, var(--sky-deep) 0%, var(--sky-mid) 40%, var(--slope-blue) 58%, var(--snow-shade) 78%, var(--snow-light) 100%);
  }
  .brand {
    position: absolute; left: 110px; top: 32px;
    font-family: "Montserrat", Arial, sans-serif; font-weight: 500;
    font-size: 31px; line-height: 45px; letter-spacing: 1.5px;
  }
  .contact-bar {
    position: absolute; left: 540px; top: 28px;
    display: flex; align-items: center; gap: 8px;
    font-size: 15.5px;
  }
  .contact-bar svg { width: 14px; height: 14px; fill: var(--accent); }
  .contact-bar .divider { margin: 0 4px; }
  .register-btn {
    position: absolute; left: 935px; top: 15px; width: 153px; height: 49px;
    border-radius: 25px; background: var(--accent);
    font-weight: 600; font-size: 15.5px; line-height: 49px; text-align: center;
  }
  .main-nav {
    position: absolute; right: 109px; top: 85px;
    display: flex; align-items: center; gap: 20px;
    font-family: "Montserrat", Arial, sans-serif; font-size: 14.5px;
  }
  .main-nav .current { color: var(--accent); }
  .main-nav svg { width: 16px; height: 16px; }
  .intro { position: absolute; left: 110px; top: 185px; width: 530px; }
  .intro .role {
    font-family: "Montserrat", Arial, sans-serif; font-size: 28px;
    color: var(--accent); letter-spacing: 1px;
  }
  .intro .name {
    font-family: "Montserrat", Arial, sans-serif; font-weight: 500;
    font-size: 47px; letter-spacing: 2px; line-height: 60px; margin-top: 6px;
    white-space: nowrap;
  }
  .intro .meta {
    display: flex; align-items: center; gap: 10px;
    font-size: 22px; margin-top: 12px; white-space: nowrap;
  }
  .meta .stars { display: flex; }
  .meta .stars svg { width: 19px; height: 19px; fill: var(--star); }
  .intro .bio {
    margin-top: 28px; width: 512px;
    font-size: 15.3px; line-height: 29px;
  }
  .actions { position: absolute; left: 111px; top: 545px; display: flex; gap: 13px; }
  .actions a {
    width: 159px; height: 55px; border: 2px solid var(--white); border-radius: 28px;
    font-weight: 600; font-size: 16px; line-height: 51px; text-align: center;
    color: var(--white); text-decoration: none;
  }
  .pointer-arrow { position: absolute; left: 565px; top: 540px; }
  .chef-portrait {
    position: absolute; left: 670px; top: 185px; width: 416px; height: 416px;
    border-radius: 50%; border: 7px solid var(--white);
    background: radial-gradient(circle at 35% 35%, #5a4a45 0%, #2b2627 45%, #1a1818 75%, #8b6651 100%);
  }
  .legal {
    position: absolute; left: 0; right: 0; top: 674px;
    text-align: center; font-size: 13px;
  }
</style>
</head>
<body>
  <div class="hero-backdrop" role="img" aria-label="Snowy Vail mountain ski slope under a deep blue sky"></div>

  <div class="brand">DECLAN<br>HARTWELL</div>

  <div class="contact-bar">
    <svg viewBox="0 0 24 24" aria-hidden="true"><path d="M6.6 10.8a15 15 0 0 0 6.6 6.6l2.2-2.2c.3-.3.7-.4 1-.2 1.1.4 2.3.6 3.6.6.6 0 1 .4 1 1V20c0 .6-.4 1-1 1A17 17 0 0 1 3 4c0-.6.4-1 1-1h3.5c.6 0 1 .4 1 1 0 1.3.2 2.5.6 3.6.1.3 0 .7-.2 1z"/></svg>
    <span>+34 611 48 27 35</span>
    <span class="divider">|</span>
    <svg viewBox="0 0 24 24" aria-hidden="true"><path d="M2 5h20v2l-10 6L2 7z"/><path d="M2 9l10 6 10-6v10H2z"/></svg>
    <span>hello@privatetable.co</span>
  </div>
  <div class="register-btn">CHEF REGISTER</div>

  <nav class="main-nav">
    <span class="current">Home</span>
    <span>Blog</span>
    <span>About me</span>
    <span>Photo gallery</span>
    <span>Recipes &amp; beer reviews</span>
    <span>Contact us</span>
    <svg viewBox="0 0 24 24" aria-hidden="true"><circle cx="10" cy="10" r="6.5" fill="none" stroke="#fff" stroke-width="3"/><path d="M15 15l6 6" stroke="#fff" stroke-width="3.2" stroke-linecap="round"/></svg>
  </nav>

  <section class="intro">
    <div class="role">CHEF</div>
    <h1 class="name">DECLAN HARTWELL</h1>
    <div class="meta">
      <span>Private Chef In Vail</span><span>|</span>
      <span class="stars">
        <svg viewBox="0 0 24 24"><path d="M12 2l3 6.6 7.2.7-5.4 4.8 1.6 7.1L12 17.5 5.6 21.2l1.6-7.1L1.8 9.3 9 8.6z"/></svg>
        <svg viewBox="0 0 24 24"><path d="M12 2l3 6.6 7.2.7-5.4 4.8 1.6 7.1L12 17.5 5.6 21.2l1.6-7.1L1.8 9.3 9 8.6z"/></svg>
        <svg viewBox="0 0 24 24"><path d="M12 2l3 6.6 7.2.7-5.4 4.8 1.6 7.1L12 17.5 5.6 21.2l1.6-7.1L1.8 9.3 9 8.6z"/></svg>
        <svg viewBox="0 0 24 24"><path d="M12 2l3 6.6 7.2.7-5.4 4.8 1.6 7.1L12 17.5 5.6 21.2l1.6-7.1L1.8 9.3 9 8.6z"/></svg>
        <svg viewBox="0 0 24 24"><path d="M12 2l3 6.6 7.2.7-5.4 4.8 1.6 7.1L12 17.5 5.6 21.2l1.6-7.1L1.8 9.3 9 8.6z"/></svg>
      </span>
      <span>5|2 Reviews</span>
    </div>
    <p class="bio">Food has been part of my life since childhood. In my late 20’s I cooked daily for touring athletes, which turned a passion into a career. I worked my way across Central America, spending years in kitchens along the coast. Vail has been my home base for some time now, apart from a year spent cooking in fine dining...</p>
  </section>

  <div class="actions">
    <a href="#">BOOK NOW!</a>
    <a href="#">READ MORE</a>
  </div>

  <svg class="pointer-arrow" width="110" height="70" viewBox="0 0 110 70" aria-hidden="true">
    <path d="M8 40 C 20 62, 60 66, 82 42 C 88 34, 90 26, 90 18" fill="none" stroke="#fff" stroke-width="5" stroke-linecap="round"/>
    <path d="M78 22 L 91 8 L 100 24" fill="none" stroke="#fff" stroke-width="5" stroke-linecap="round" stroke-linejoin="round"/>
  </svg>

  <div class="chef-portrait" role="img" aria-label="Portrait of the chef beside a whole roast in a smoker"></div>

  <footer class="legal">Copyrights © 2019, Declan Hartwell. All Rights Reserved.</footer>
</body>
</html>
```